Automotive component supplier needs a business card design

We need a business card design for our company called Velran Global Components Ltd based in the UK. We are a supplier of interior and exterior components to premium car manufacturers such as Corvel Ashby, Hadley Fenn, Marquist and Tavarelli. We would like to see a modern business card design that uses the colour blue.

Target Market(s)

Premium automotive car manufacturers.

Industry/Entity Type

Automotive

Contact Information for Business Card

Company Name : Velran Global Components Limited
Address: 17 Marlow Yard, Upper Heath, Warwick, CV31 8QL, United Kingdom
Web Address : www.velrancomponents-example.co.uk

Font styles to use
Other font styles liked:
• Helvetica

Colors
3176b5
0255a3
85acd3
cfdeed
cee9f5
85cae6
34a6d7
0692cd
9bcb3c

Requirements
Must have
• Clear company logo and a mixture of blue colours.
Nice to have
• A high quality modern image.
Should not have
• Multiple colours.

```html
<!DOCTYPE html>
<html lang="en">
<head>
<meta charset="utf-8">
<title>Velran Global Components – Business Card</title>
<link rel="stylesheet" href="https://fonts.googleapis.com/css2?family=Lato:wght@400;700&display=swap">
<style>
  :root {
    --brand-blue: #0a8ad0;
    --deep-blue: #0255a3;
    --accent-green: #9bcb3c;
    --ink: #2b2b2b;
    --rule: #8a8a8a;
    --paper: #ffffff;
    --backdrop: #e6e8eb;
  }
  * { box-sizing: border-box; margin: 0; padding: 0; }
  html, body { width: 1200px; height: 800px; overflow: hidden; }
  body {
    background: var(--backdrop);
    font-family: "Lato", Helvetica, Arial, sans-serif;
    display: flex;
    align-items: center;
    justify-content: center;
    gap: 50px;
  }
  .card {
    position: relative;
    width: 525px;
    height: 300px;
    overflow: hidden;
    box-shadow: 0 6px 18px rgba(0,0,0,0.18);
  }

  /* Front */
  .card--front {
    background: var(--brand-blue);
    color: var(--paper);
    display: flex;
    flex-direction: column;
    align-items: center;
  }
  .front-brand {
    margin-top: 92px;
    display: flex;
    align-items: center;
    gap: 12px;
  }
  .brand-mark {
    width: 14px;
    height: 14px;
    background: var(--accent-green);
  }
  .brand-name {
    font-weight: 700;
    font-size: 30px;
    letter-spacing: 0.5px;
    text-transform: uppercase;
  }
  .front-web {
    position: absolute;
    bottom: 54px;
    width: 100%;
    text-align: center;
    font-size: 13px;
    letter-spacing: 1.5px;
  }

  /* Back */
  .card--back { background: var(--paper); color: var(--ink); }
  .back-brand {
    position: absolute;
    top: 48px;
    right: 34px;
    display: flex;
    align-items: center;
    gap: 10px;
  }
  .back-brand .brand-name { color: var(--brand-blue); font-size: 24px; }
  .brand-rule {
    position: absolute;
    top: 100px;
    right: 34px;
    width: 250px;
    border-top: 1px solid var(--rule);
  }
  .person {
    position: absolute;
    top: 136px;
    left: 36px;
    width: 455px;
    display: flex;
    align-items: baseline;
    gap: 6px;
    padding-bottom: 6px;
    border-bottom: 1px solid var(--rule);
  }
  .person-name { color: var(--brand-blue); font-size: 20px; }
  .person-divider { color: var(--brand-blue); font-size: 18px; }
  .person-role { font-size: 14px; }
  .contacts {
    position: absolute;
    top: 180px;
    left: 36px;
    list-style: none;
    font-size: 13px;
    line-height: 19px;
  }
  .contacts li { display: flex; align-items: center; gap: 9px; }
  .contacts svg { width: 12px; height: 12px; fill: var(--brand-blue); flex: none; }
  .address {
    position: absolute;
    top: 178px;
    right: 34px;
    text-align: right;
    font-size: 13px;
    line-height: 17px;
    font-style: normal;
  }
  .base-band { position: absolute; left: 0; bottom: 0; width: 525px; height: 62px; }
</style>
</head>
<body>

<section class="card card--front" aria-label="Card front">
  <div class="front-brand">
    <span class="brand-mark"></span>
    <span class="brand-name">Velran Global Components</span>
  </div>
  <p class="front-web">www.velrancomponents-example.co.uk</p>
</section>

<section class="card card--back" aria-label="Card back">
  <div class="back-brand">
    <span class="brand-mark"></span>
    <span class="brand-name">Velran Global Components</span>
  </div>
  <div class="brand-rule"></div>

  <div class="person">
    <span class="person-name">Rowan Teague</span>
    <span class="person-divider">|</span>
    <span class="person-role">Manager</span>
  </div>

  <ul class="contacts">
    <li>
      <svg viewBox="0 0 24 24"><path d="M6.6 10.8a15.1 15.1 0 0 0 6.6 6.6l2.2-2.2a1 1 0 0 1 1-.25 11.4 11.4 0 0 0 3.6.57 1 1 0 0 1 1 1V20a1 1 0 0 1-1 1A17 17 0 0 1 3 4a1 1 0 0 1 1-1h3.5a1 1 0 0 1 1 1c0 1.25.2 2.45.57 3.57a1 1 0 0 1-.25 1z"/></svg>
      512 004 2710
    </li>
    <li>
      <svg viewBox="0 0 24 24"><path d="M7 1h10a2 2 0 0 1 2 2v18a2 2 0 0 1-2 2H7a2 2 0 0 1-2-2V3a2 2 0 0 1 2-2zm0 3v14h10V4zm5 15.5a1.2 1.2 0 1 0 0 2.4 1.2 1.2 0 0 0 0-2.4z"/></svg>
      512 004 2711
    </li>
    <li>
      <svg viewBox="0 0 24 24"><path d="M2 5h20v14H2zm2 2v.5l8 5 8-5V7zm0 2.8V17h16V9.8l-8 5z"/></svg>
      info@velrancomponents-example.co.uk
    </li>
    <li>
      <svg viewBox="0 0 24 24"><path d="M12 2a10 10 0 1 0 0 20 10 10 0 0 0 0-20zm6.9 6h-3a15.6 15.6 0 0 0-1.4-3.6A8 8 0 0 1 18.9 8zM12 4c.8 1.2 1.5 2.5 1.9 4h-3.8c.4-1.5 1.1-2.8 1.9-4zM4.3 14a8 8 0 0 1 0-4h3.4a16 16 0 0 0 0 4zm.8 2h3a15.6 15.6 0 0 0 1.4 3.6A8 8 0 0 1 5.1 16zm3-8h-3a8 8 0 0 1 4.4-3.6A15.6 15.6 0 0 0 8.1 8zM12 20c-.8-1.2-1.5-2.5-1.9-4h3.8c-.4 1.5-1.1 2.8-1.9 4zm2.3-6H9.7a14 14 0 0 1 0-4h4.6a14 14 0 0 1 0 4zm.2 5.6a15.6 15.6 0 0 0 1.4-3.6h3a8 8 0 0 1-4.4 3.6zm1.8-5.6a16 16 0 0 0 0-4h3.4a8 8 0 0 1 0 4z"/></svg>
      www.velrancomponents-example.co.uk
    </li>
  </ul>

  <address class="address">
    17 Marlow Yard, Upper Heath<br>
    Warwick, CV31 8QL<br>
    United Kingdom
  </address>

  <svg class="base-band" viewBox="0 0 525 62" preserveAspectRatio="none" aria-hidden="true">
    <polygon points="0,46 370,20 525,20 525,62 0,62" fill="var(--brand-blue)"/>
    <polygon points="0,38 340,24 360,28 0,50" fill="var(--accent-green)"/>
    <polygon points="0,30 360,22 380,14 525,14 525,20 370,20 0,46" fill="var(--paper)"/>
  </svg>
</section>

</body>
</html>
```